Tessel - Web Design Project

We are seeking to have our website redesigned. Our current webpage is rather dated looking www.tessel-momentum.example We will be utilizing similar content to explain our services as what is in the website now. We do not see it at a retail portal but rather a website for those inquiring about our services as a reference check so to speak.

We wish to have a look that is considered clean, fresh, contemporary and contains a business savvy vibe.

We prefer isolated white background and also wish to retain the integrity of our Logo and colour scheme.

We are looking for something that doesnt look like it was designed at home on sitenook. We are hoping to find something that looks like it would reside on a tablet.

Hello designers!

We apologize for our tardiness as we have been quite preoccupied. We will be extending our invites to the end of January!

Hello All,

Please review our offer once again for updated requirements.  We are hoping to accept a design by months end.

Tessel

Target Market(s)

Business to business clients and Large manufacturers

Industry/Entity Type

Retail

Requirements
Must have
• Existing Logo

There must be an area dedicated to an intro video that will be incorporated on our landing page.

We require design of the other pages as well not only the landing page.

```html
<!DOCTYPE html>
<html lang="en">
<head>
<meta charset="utf-8">
<title>Tessel Performance Group</title>
<link rel="stylesheet" href="https://fonts.googleapis.com/css2?family=Arvo&family=PT+Sans:wght@400;700&display=swap">
<style>
:root{
  --page-dark:#1b1b1b;
  --page-dark-2:#2b2b2b;
  --white:#ffffff;
  --ink:#3a3a3a;
  --ink-soft:#555555;
  --text-grey:#6a6a6a;
  --red:#e0281a;
  --red-dark:#c81f0c;
  --nav-top:#ee3b1c;
  --nav-bottom:#d52a10;
  --panel:#f3f3f3;
  --panel-2:#ececec;
  --field:#7a7a7a;
  --btn-top:#3e4245;
  --btn-bottom:#141617;
}
*{box-sizing:border-box;margin:0;padding:0}
html,body{width:1200px;height:951px;overflow:hidden}
body{
  position:relative;
  background:radial-gradient(ellipse at center,var(--page-dark-2),var(--page-dark) 70%);
  font-family:"PT Sans",sans-serif;color:var(--ink);
}
.site{position:absolute;left:120px;top:0;width:960px;height:951px;background:var(--white)}
.abs{position:absolute}

/* justified text set line by line */
.line{display:block;white-space:nowrap;text-align:justify;text-align-last:justify}
.line-last{display:block;white-space:nowrap}

/* header */
.brand{left:48px;top:22px;display:flex;align-items:center;gap:10px}
.brand-dot{width:14px;height:14px;border-radius:50%;background:var(--red)}
.brand-name{font-size:52px;font-weight:700;color:#4a4546;line-height:1;letter-spacing:-1px}
.phone{right:12px;top:34px;font-size:19px;color:var(--ink)}
.search{left:676px;top:74px;width:272px;height:23px;border-radius:4px;
  background:linear-gradient(#4a4d50,#2c2e30);color:#fff;font-size:12px;padding:4px 10px;display:flex;justify-content:space-between;align-items:center}

/* nav */
.main-nav{left:0;top:108px;width:962px;height:39px;background:linear-gradient(var(--nav-top),var(--nav-bottom));
  font-size:14px;font-weight:700;color:#fff;text-transform:uppercase}
.main-nav a{color:#fff;text-decoration:none;position:absolute;top:0;height:39px;line-height:40px}
.main-nav .active{background:var(--red-dark);left:0;width:93px;text-align:center;border-right:1px solid #a81a08}

/* hero */
.hero{left:0;top:147px;width:960px;height:374px;background:linear-gradient(#fff 85%,#e9e9e9)}
.hero-frame{left:19px;top:26px;width:517px;height:307px;border:1px solid #c9c9c9;border-radius:3px;background:linear-gradient(#f4f4f4,#e2e2e2)}
.hero-video{left:10px;top:10px;width:495px;height:285px;
  background:linear-gradient(160deg,#3a3f4a 0%,#2b2a25 35%,#7a4a1e 60%,#e87a1e 75%,#2a2a24 100%)}
.welcome{left:557px;top:21px;width:370px}
.welcome h1{font-weight:400;font-size:28px;line-height:28px;color:var(--ink)}
.welcome h1 span{display:block;color:var(--red)}
.welcome .rule{height:2px;background:#555;margin-top:10px}
.welcome p{font-size:14.6px;line-height:24px;color:var(--ink-soft);margin-top:9px}
.btn{display:block;border-radius:3px;background:linear-gradient(var(--btn-top),var(--btn-bottom));color:#fff;font-weight:700;text-align:center}
.btn-lg{left:557px;top:301px;width:140px;height:30px;line-height:30px;font-size:15px}

/* lower */
.lower{left:0;top:521px;width:960px;height:349px;background:var(--panel)}
.services{left:19px;top:21px;width:603px;height:318px;border:2px solid #dedede;border-radius:3px;background:#f3f3f3}
.section-title{font-family:"Arvo",serif;font-size:20px;color:var(--red);font-weight:400}
.services .section-title{left:14px;top:11px}
.thumb{border:1px solid #d6d6d6;background:#fff;padding:5px}
.thumb .photo{width:100%;height:100%}
.thumb-1{left:13px;top:47px;width:277px;height:99px}
.thumb-1 .photo{background:linear-gradient(#e8eaec 25%,#7f8288 45%,#3d3f43 80%,#9a9ca0)}
.thumb-2{left:314px;top:47px;width:271px;height:99px}
.thumb-2 .photo{background:linear-gradient(100deg,#1a2a6a,#3b62c9 45%,#0d1640 70%,#2a3f9a)}
.card-title{font-family:Arial,sans-serif;font-weight:700;font-size:16.5px;color:#333}
.card-text{font-family:Arial,sans-serif;font-size:12.8px;line-height:20.5px;color:var(--text-grey);width:275px}
.btn-sm{width:90px;height:28px;line-height:28px;font-size:12.5px}
.btn-red{background:linear-gradient(#e93a1d,#c8200a)}
.contact{left:639px;top:22px;width:294px;height:315px;background:var(--panel-2)}
.contact .section-title{left:20px;top:9px}
.contact p{left:22px;top:46px;width:256px;font-size:13px;line-height:16px;color:#333}
.field{left:21px;width:250px;border-radius:4px;background:var(--field);color:#fff;font-size:14px;padding:2px 13px;box-shadow:inset 0 1px 2px rgba(0,0,0,.3)}

/* footer */
.footer{left:0;top:870px;width:960px;height:81px;background:var(--panel);border-top:2px solid #e0e0e0}
.footer-nav{left:0;top:13px;width:960px;text-align:center;font-size:16.5px;font-weight:700;color:#555;white-space:nowrap}
.footer-nav .sep{margin:0 19px}
.copyright{left:0;top:47px;width:960px;text-align:center;font-size:14px;color:#555;letter-spacing:.3px}
</style>
</head>
<body>
<div class="site">
  <header>
    <div class="abs brand"><span class="brand-dot"></span><span class="brand-name">tessel</span></div>
    <div class="abs phone">555-010-0199</div>
    <div class="abs search"><span>Start searching...</span>
      <svg width="13" height="13" viewBox="0 0 13 13"><circle cx="7.5" cy="5.5" r="4" fill="none" stroke="#ddd" stroke-width="1.5"/><line x1="4.6" y1="8.4" x2="1" y2="12" stroke="#ddd" stroke-width="2"/></svg>
    </div>
  </header>

  <nav class="abs main-nav">
    <a class="active">Home</a>
    <a style="left:121px">Who We Are?</a>
    <a style="left:272px">Cross the Tessel</a>
    <a style="left:454px">Performance Solutions</a>
    <a style="left:687px">Sustain Solutions</a>
    <a style="left:878px">Join Us</a>
  </nav>

  <section class="abs hero">
    <div class="abs hero-frame">
      <div class="abs hero-video" role="img" aria-label="Intro video area: night highway with orange and white light trails"></div>
    </div>
    <div class="abs welcome">
      <h1>Welcome to<span>Tessel Performance Group</span></h1>
      <div class="rule"></div>
      <p>
        <span class="line">Tessel Performance Group Inc. is the leading provider of</span>
        <span class="line">profit generating and people development solutions. With</span>
        <span class="line">the hands-on experience of best practices, the</span>
        <span class="line">state-of-the-art technology and in-depth information we</span>
        <span class="line">help companies increase their efficiencies and profits. Frank,</span>
        <span class="line">honest, committed, valuable and rewarding are words that</span>
        <span class="line">customers use to describe the quality services provided by</span>
        <span class="line-last">Tessel Performance Group.</span>
      </p>
    </div>
    <a class="abs btn btn-lg">Read More</a>
  </section>

  <section class="abs lower">
    <div class="abs services">
      <h2 class="abs section-title">Our Services And Solutions</h2>
      <div class="abs thumb thumb-1"><div class="photo" role="img" aria-label="Coastal road curving along the sea"></div></div>
      <div class="abs thumb thumb-2"><div class="photo" role="img" aria-label="Car interior at speed with blue light streaks"></div></div>
      <h3 class="abs card-title" style="left:14px;top:158px">Performance Solutions</h3>
      <p class="abs card-text" style="left:15px;top:186px">
        <span class="line">We will work together with you to identify your</span>
        <span class="line">needs, challenges and opportunities. We will</span>
        <span class="line">then recommend the next steps and work with</span>
        <span class="line-last">you to develop your bespoke.....</span>
      </p>
      <a class="abs btn btn-sm" style="left:13px;top:277px">Read More</a>
      <h3 class="abs card-title" style="left:313px;top:158px">Sustain Solutions</h3>
      <p class="abs card-text" style="left:314px;top:186px;width:268px">
        <span class="line">We understand that consulting and training</span>
        <span class="line">work very well when on site but we also under-</span>
        <span class="line">stand that some learning can be accomplished</span>
        <span class="line-last">as effectively by other means.......</span>
      </p>
      <a class="abs btn btn-sm btn-red" style="left:314px;top:277px">Read More</a>
    </div>

    <div class="abs contact">
      <h2 class="abs section-title">Cross the Tessel</h2>
      <svg class="abs" style="left:227px;top:13px" width="30" height="22" viewBox="0 0 30 22"><rect x="1" y="3" width="26" height="17" fill="#fff" stroke="#777"/><polyline points="1,3 14,13 27,3" fill="none" stroke="#777"/></svg>
      <p class="abs">Contact us with your request and we will make sure your needs are met as soon as possible.</p>
      <div class="abs field" style="top:110px;height:23px">Name</div>
      <div class="abs field" style="top:140px;height:23px">E-mail</div>
      <div class="abs field" style="top:170px;height:98px;padding-top:5px">Comments</div>
      <a class="abs btn btn-sm" style="left:21px;top:278px">Send it!!</a>
    </div>
  </section>

  <footer class="abs footer">
    <div class="abs footer-nav">Home<span class="sep">|</span>Who We Are?<span class="sep">|</span>Cross The Tessel<span class="sep">|</span>Performane Solutions<span class="sep">|</span>Sustain Solutions<span class="sep">|</span>Join Us</div>
    <div class="abs copyright">Copyright © 2012 tessel-momentum.example. All Rights Reserved.</div>
  </footer>
</div>
</body>
</html>
```